Velmora Systems Website

Website design for our company: Velmora Systems.
The website should look fresh and IT focused. Please have a look at http://www.velmorasystems.example.au/ for our current design. We want something fresh and new, professional looking, in WordPress so we can easily make changes.

It Company

```html
<!DOCTYPE html>
<html lang="en">
<head>
<meta charset="utf-8">
<title>Velmora Systems</title>
<link href="https://fonts.googleapis.com/css2?family=Open+Sans:ital,wght@0,300;0,400;0,600;1,400&display=swap" rel="stylesheet">
<style>
:root{
  --green:#05b157;
  --green-dark:#039a4a;
  --text:#8a8f95;
  --heading:#4a4f55;
  --line:#e6e8ea;
  --bg:#f9fafb;
  --footer:#3a3f47;
  --footer-bottom:#30343b;
  --footer-text:#8f949b;
  --link:#2fa3d8;
}
*{margin:0;padding:0;box-sizing:border-box}
html,body{width:1024px;height:1200px;overflow:hidden}
body{position:relative;background:var(--bg);font-family:"Open Sans",Arial,sans-serif;color:var(--text)}
.abs{position:absolute}
.topbar{left:0;top:0;width:1024px;height:31px;background:var(--green)}
.search{left:726px;top:3px;width:162px;height:24px;background:#fff;border:1px solid #cfe9d8;border-radius:2px;font-size:9px;color:#999;padding:5px 0 0 27px}
.search svg{position:absolute;left:8px;top:5px}
.navbar{left:0;top:31px;width:1024px;height:61px;background:#fff}
.logo{left:136px;top:12px;width:150px;height:74px;background:var(--green);border:3px solid #fff;border-radius:4px;box-shadow:0 1px 4px rgba(0,0,0,.25);display:flex;align-items:center;justify-content:center;gap:6px;color:#fff;font-weight:600;font-size:14px}
.logo .dot{width:12px;height:12px;border-radius:50%;background:#fff}
.nav{left:301px;top:31px;height:61px;display:flex;border-left:1px solid var(--line)}
.nav a{display:flex;align-items:center;justify-content:center;height:61px;border-right:1px solid var(--line);font-size:12px;font-weight:600;color:#777;text-decoration:none}
.nav a.active{color:var(--green)}
.hero{left:0;top:92px;width:1024px;height:378px;background:linear-gradient(180deg,#3f74b8 0%,#7ea8d6 45%,#c4d6e6 72%,#7d8f6a 92%,#5f8a3e 100%)}
.hero h1{left:178px;top:198px;font-weight:300;font-size:29px;line-height:39px;color:#fff}
.btn{display:flex;align-items:center;justify-content:center;background:linear-gradient(#fff,#ececec);border:1px solid #c9cccf;border-radius:3px;box-shadow:0 1px 2px rgba(0,0,0,.15);font-size:11.5px;color:#777}
.card{top:437px;width:233px;height:315px;background:#fff;border-radius:5px;box-shadow:0 1px 3px rgba(0,0,0,.08)}
.card h2{position:absolute;font-weight:300;font-size:19px;color:var(--heading)}
.about-photo{left:16px;top:61px;width:200px;height:102px;background:linear-gradient(135deg,#dfe6ee,#8a96a6 60%,#2a3242)}
.about-text{left:16px;top:179px;width:205px;font-size:11.5px;line-height:16px}
.services{left:24px;top:64px;list-style:none;font-size:11.5px}
.services li{height:24px;display:flex;align-items:center;gap:7px}
.remote-head{left:0;top:0;width:233px;height:107px;background:linear-gradient(#2ccf73,var(--green));border-radius:5px 5px 0 0;border-bottom:2px solid var(--green-dark)}
.remote-icon{left:19px;top:25px;width:51px;height:50px;background:var(--green-dark);border-radius:4px;box-shadow:inset 0 1px 2px rgba(0,0,0,.2)}
.remote-head h2{left:78px;top:22px;color:#fff}
.remote-head p{position:absolute;left:81px;top:61px;font-size:9.5px;line-height:14px;color:#0c3a1e}
.code{left:20px;top:129px;width:196px;height:38px;border:1px solid #d3d6d9;border-radius:2px;font-size:11px;color:#c5c9cd;padding:10px 0 0 46px;letter-spacing:1px}
.code svg{position:absolute;left:18px;top:11px}
.divider{left:0;width:233px;height:1px;background:var(--line)}
.contact-line{left:20px;font-size:11.5px}
.contact-line a{color:var(--link);text-decoration:none}
.section-title{font-weight:300;font-size:19px;color:var(--heading)}
.quote{left:140px;top:822px;width:488px;height:106px;background:#ebecee;padding:17px 20px 0 24px;font-style:italic;font-size:11.5px;line-height:21px;color:#888}
.cite{left:226px;top:939px;font-style:italic;font-size:10px;color:#777}
.client{display:flex;align-items:center;justify-content:center;gap:6px;font-weight:600;color:#fff;font-size:12px;text-align:center}
.footer{left:0;top:999px;width:1024px;height:166px;background:var(--footer)}
.footer-bottom{left:0;top:1165px;width:1024px;height:35px;background:var(--footer-bottom)}
.flogo{left:136px;top:1031px;width:149px;height:76px;background:#63676d;border:2px solid #55595f;border-radius:4px;display:flex;align-items:center;justify-content:center;gap:6px;color:#a6aab0;font-weight:600;font-size:14px}
.flogo .dot{width:12px;height:12px;border-radius:50%;background:#a6aab0}
.fh{font-size:11px;color:#c9ccd0;top:1030px}
.flist{font-size:10.5px;line-height:19px;color:var(--footer-text);list-style:none;top:1056px}
.flist .on{color:#fff}
.legal{font-size:8.5px;color:#6c7077;top:1178px}
</style>
</head>
<body>
<div class="abs topbar"></div>
<div class="abs search">
  <svg width="12" height="12" viewBox="0 0 12 12"><circle cx="5" cy="5" r="4" fill="none" stroke="#05b157" stroke-width="1.3"/><line x1="8" y1="8" x2="11" y2="11" stroke="#05b157" stroke-width="1.3"/></svg>
  Search
</div>
<div class="abs navbar"></div>
<div class="abs logo"><span class="dot"></span>Velmora Systems</div>
<nav class="abs nav">
  <a class="active" style="width:72px">Home</a>
  <a style="width:92px">Services</a>
  <a style="width:82px">Support</a>
  <a style="width:76px">Clients</a>
  <a style="width:105px">Testimonial</a>
  <a style="width:78px">About</a>
  <a style="width:83px">Contact</a>
</nav>

<div class="abs hero" role="img" aria-label="Smiling professional in front of a sunny city skyline with towers and a stadium"></div>
<h1 class="abs hero-title" style="left:178px;top:198px;font-weight:300;font-size:29px;line-height:39px;color:#fff">We Bring Your Business<br>Forward with Our Solutions</h1>
<div class="abs btn" style="left:180px;top:299px;width:88px;height:31px">Contact Us</div>

<section class="abs card" style="left:140px">
  <h2 style="left:16px;top:22px">About Velmora Systems</h2>
  <div class="abs about-photo" role="img" aria-label="Business team meeting around a table"></div>
  <p class="abs about-text">Velmora Systems is an Adelaide based company with a single objective - to excel in the support and service of all computer and IT needs.</p>
  <div class="abs btn" style="left:14px;top:266px;width:88px;height:31px">Read More</div>
</section>

<section class="abs card" style="left:395px">
  <h2 style="left:27px;top:22px">Our Services</h2>
  <ul class="abs services">
    <li><svg width="10" height="10" viewBox="0 0 10 10"><circle cx="5" cy="5" r="3.2" fill="#b9bdc2"/><circle cx="5" cy="5" r="4.6" fill="none" stroke="#b9bdc2" stroke-width="1.4" stroke-dasharray="1.6 1.3"/></svg>On-site Service</li>
    <li><svg width="10" height="10" viewBox="0 0 10 10"><circle cx="5" cy="5" r="3.2" fill="#b9bdc2"/><circle cx="5" cy="5" r="4.6" fill="none" stroke="#b9bdc2" stroke-width="1.4" stroke-dasharray="1.6 1.3"/></svg>Remote Desktop Support</li>
    <li><svg width="10" height="10" viewBox="0 0 10 10"><circle cx="5" cy="5" r="3.2" fill="#b9bdc2"/><circle cx="5" cy="5" r="4.6" fill="none" stroke="#b9bdc2" stroke-width="1.4" stroke-dasharray="1.6 1.3"/></svg>Medical IT Service</li>
    <li><svg width="10" height="10" viewBox="0 0 10 10"><circle cx="5" cy="5" r="3.2" fill="#b9bdc2"/><circle cx="5" cy="5" r="4.6" fill="none" stroke="#b9bdc2" stroke-width="1.4" stroke-dasharray="1.6 1.3"/></svg>Pharmacy IT Service</li>
    <li><svg width="10" height="10" viewBox="0 0 10 10"><circle cx="5" cy="5" r="3.2" fill="#b9bdc2"/><circle cx="5" cy="5" r="4.6" fill="none" stroke="#b9bdc2" stroke-width="1.4" stroke-dasharray="1.6 1.3"/></svg>Website Design</li>
    <li><svg width="10" height="10" viewBox="0 0 10 10"><circle cx="5" cy="5" r="3.2" fill="#b9bdc2"/><circle cx="5" cy="5" r="4.6" fill="none" stroke="#b9bdc2" stroke-width="1.4" stroke-dasharray="1.6 1.3"/></svg>Disaster Recovery</li>
    <li><svg width="10" height="10" viewBox="0 0 10 10"><circle cx="5" cy="5" r="3.2" fill="#b9bdc2"/><circle cx="5" cy="5" r="4.6" fill="none" stroke="#b9bdc2" stroke-width="1.4" stroke-dasharray="1.6 1.3"/></svg>Hardware/ Software supply</li>
    <li><svg width="10" height="10" viewBox="0 0 10 10"><circle cx="5" cy="5" r="3.2" fill="#b9bdc2"/><circle cx="5" cy="5" r="4.6" fill="none" stroke="#b9bdc2" stroke-width="1.4" stroke-dasharray="1.6 1.3"/></svg>Consumables</li>
  </ul>
  <div class="abs btn" style="left:14px;top:266px;width:88px;height:31px">Read More</div>
</section>

<section class="abs card" style="left:650px">
  <div class="abs remote-head">
    <div class="abs remote-icon">
      <svg width="51" height="50" viewBox="0 0 51 50"><ellipse cx="22" cy="22" rx="11" ry="8" fill="#fff"/><path d="M16 28 l-3 6 l8-4z" fill="#fff"/><ellipse cx="31" cy="28" rx="9" ry="6.5" fill="#e8f5ec" stroke="#039a4a" stroke-width="1.5"/><path d="M35 33 l4 5 l-1-6z" fill="#e8f5ec"/></svg>
    </div>
    <h2>Remote Support</h2>
    <p>Enter Your 6 digit code to<br>connect our support</p>
  </div>
  <div class="abs code">
    <svg width="13" height="15" viewBox="0 0 13 15"><rect x="1" y="6" width="11" height="8" rx="1" fill="none" stroke="#2fa3d8" stroke-width="1.3"/><path d="M3.5 6 V4 a3 3 0 0 1 6 0" fill="none" stroke="#2fa3d8" stroke-width="1.3"/></svg>
    ******
  </div>
  <div class="abs btn" style="left:20px;top:181px;width:88px;height:31px">Connect</div>
  <div class="abs divider" style="top:229px"></div>
  <p class="abs contact-line" style="top:244px">Phone: (+61)1800.555.0142</p>
  <div class="abs divider" style="top:272px"></div>
  <p class="abs contact-line" style="top:283px">E-mail: <a>info@velmorasystems.example.au</a></p>
</section>

<h3 class="abs section-title" style="left:154px;top:782px">Testimonials</h3>
<blockquote class="abs quote">"I have always found the team extremely helpful with their advice over the phone. They also have the ability to access our computers remotely, and can rectify most problems quite swiftly. I have no hesitation in recommending Velmora Systems for all of your IT needs."</blockquote>
<svg class="abs" style="left:568px;top:928px" width="24" height="21" viewBox="0 0 24 21"><path d="M0 0 H24 L0 21z" fill="#ebecee"/></svg>
<p class="abs cite"><span style="font-style:normal;font-weight:600;margin-right:6px">&#10077;</span>Daniel Ferrow of Brightwell Chemists, Kestrel Vale</p>

<h3 class="abs section-title" style="left:660px;top:782px">Our Clients</h3>
<div class="abs client" style="left:650px;top:822px;width:127px;height:65px;background:#b4b7ba">Harbourline<br>Chemists</div>
<div class="abs client" style="left:799px;top:822px;width:89px;height:68px;color:#8d9196;font-weight:400;font-size:11px">Corvale<br>Pharmacy Services</div>
<div class="abs client" style="left:650px;top:902px;width:240px;height:61px;background:#e6e7e8;color:#9a9ea3;font-size:14px"><span style="width:12px;height:12px;border-radius:50%;background:#9a9ea3"></span>Ardent &amp; Rowe Health Group</div>

<footer>
  <div class="abs footer"></div>
  <div class="abs flogo"><span class="dot"></span>Velmora Systems</div>
  <h4 class="abs fh" style="left:329px;font-weight:400">NAVIGATION</h4>
  <ul class="abs flist" style="left:329px"><li>Home</li><li class="on">Clients</li><li>Services</li><li>Support</li></ul>
  <ul class="abs flist" style="left:418px"><li>Testimonials</li><li>About</li><li>Contact Us</li></ul>
  <h4 class="abs fh" style="left:521px;font-weight:400">WHERE WE ARE</h4>
  <ul class="abs flist" style="left:522px"><li>PO Box 40318</li><li>Larkspur Lane, Melbourne</li><li>Victoria 3999 Australia</li></ul>
  <h4 class="abs fh" style="left:714px;font-weight:400">CONTACT US</h4>
  <ul class="abs flist" style="left:714px"><li>Phone: (03) 5550 1827</li><li>support@velmorasystems.example.au</li></ul>
  <div class="abs footer-bottom"></div>
  <p class="abs legal" style="left:136px">COPYRIGHT - 2014 - VELMORA SYSTEMS</p>
  <p class="abs legal" style="left:717px">PRIVACY POLICY | SITEMAP</p>
</footer>
</body>
</html>
```